Banner poster with different motifs

I'm looking for 5 banners and posters in A1 format in the same design, or the similarity must be recognizable...
Kept quite simple with different titles.

1 ballet
2 Contemporary Dance
3 high heels
4 Salsa & Bachata & Zouk
5 Hip Hop

Modern bright colors
it is for the entrance so that the students see here is a dance school

The text may also be included in the image
The photos are for guidance only; some are our own, some are purchased. However, we are permitted to use them, including our logo, of course.

```html
<!DOCTYPE html>
<html lang="en">
<head>
<meta charset="utf-8">
<title>High Heels – Solena Dance Center</title>
<link href="https://fonts.googleapis.com/css2?family=Bebas+Neue&family=Montserrat:wght@300;500;600&display=swap" rel="stylesheet">
<style>
  :root {
    --stage: #bcbcbc;
    --navy-deep: #0a1f4a;
    --navy: #123a73;
    --navy-mid: #1b4a86;
    --magenta: #b21fc4;
    --violet: #5a2590;
    --white: #ffffff;
    --ice: #b3e7ff;
    --ice-glow: rgba(120, 210, 255, 0.85);
    --photo-dark: #1a1a22;
    --photo-skin: #a8806c;
  }
  * { margin: 0; padding: 0; box-sizing: border-box; }
  html, body {
    width: 1200px;
    height: 956px;
    overflow: hidden;
    background: var(--stage);
  }
  .poster {
    position: absolute;
    left: 20px;
    top: 68px;
    width: 1160px;
    height: 819px;
    overflow: hidden;
    font-family: "Montserrat", sans-serif;
    background:
      radial-gradient(ellipse 170px 120px at 210px 440px, rgba(200, 40, 210, 0.85), transparent 70%),
      radial-gradient(ellipse 330px 220px at 250px 470px, rgba(110, 40, 170, 0.7), transparent 75%),
      radial-gradient(ellipse 420px 300px at 900px 300px, rgba(40, 90, 160, 0.45), transparent 75%),
      radial-gradient(ellipse 600px 260px at 500px 780px, rgba(8, 25, 60, 0.7), transparent 80%),
      linear-gradient(160deg, var(--navy-deep) 0%, var(--navy) 45%, var(--navy-mid) 70%, var(--navy-deep) 100%);
  }
  .title-high {
    position: absolute;
    left: 124px;
    top: 8px;
    font-weight: 500;
    font-size: 262px;
    line-height: 1;
    letter-spacing: 6px;
    color: var(--white);
  }
  .dancer-photo {
    position: absolute;
    left: 414px;
    top: 93px;
    width: 560px;
    height: 726px;
    border-radius: 46% 46% 8% 8% / 18% 18% 4% 4%;
    background:
      radial-gradient(ellipse 90px 110px at 180px 120px, var(--photo-skin), transparent 75%),
      linear-gradient(180deg, #2a2530 0%, var(--photo-dark) 55%, #0d0d12 100%);
    opacity: 0.92;
  }
  .title-heels {
    position: absolute;
    left: 282px;
    top: 398px;
    font-family: "Bebas Neue", sans-serif;
    font-size: 394px;
    line-height: 0.82;
    letter-spacing: 10px;
    color: var(--ice);
    text-shadow: 0 0 14px var(--ice-glow), 0 0 30px rgba(90, 190, 255, 0.55);
  }
  .brand {
    position: absolute;
    left: 850px;
    top: 58px;
    width: 250px;
    text-align: center;
    color: var(--white);
  }
  .brand-circle {
    display: block;
    width: 74px;
    height: 74px;
    margin: 0 auto 20px;
    border: 2px solid var(--white);
    border-radius: 50%;
  }
  .brand-name {
    font-weight: 300;
    font-size: 36px;
    letter-spacing: 4px;
    line-height: 1;
  }
  .brand-tagline {
    margin-top: 8px;
    font-weight: 300;
    font-size: 11px;
    letter-spacing: 2.4px;
    text-transform: uppercase;
  }
  .website {
    position: absolute;
    left: 74px;
    top: 732px;
    font-weight: 500;
    font-size: 20px;
    letter-spacing: 3.4px;
    color: var(--white);
  }
</style>
</head>
<body>
  <main class="poster">
    <h1 class="title-high">HIGH</h1>
    <div class="dancer-photo" role="img" aria-label="Photo of a kneeling dancer in a black bodysuit, long glossy black gloves and thigh-high boots"></div>
    <h2 class="title-heels">HEELS</h2>
    <div class="brand">
      <span class="brand-circle"></span>
      <p class="brand-name">SOLENA</p>
      <p class="brand-tagline">Dance Center Mainfeld</p>
    </div>
    <p class="website">www.solena-dance.com</p>
  </main>
</body>
</html>
```